Business Card for Industrial Distributor

We need a business card design for an industrial distributor. We sell machine parts for the manufacturing and oil industry. We would like the cards to look clean and modern but with a touch of industry.

Our colors are blue/white.

Please feel free to visit our website www.korvelpartsco.com

Target Market(s)

mexican manufacturers in the automobile/aerospace industry

Industry/Entity Type

Industrial

Colors
ffffff
0555a3

```html
<!DOCTYPE html>
<html lang="en">
<head>
<meta charset="utf-8">
<title>Korvel Business Card</title>
<link rel="stylesheet" href="https://fonts.googleapis.com/css2?family=Montserrat:wght@500;700;800&family=Lato:wght@400;700&display=swap">
<style>
  :root {
    --stage: #e9ebef;
    --card-white: #ffffff;
    --navy: #2a2e94;
    --brand-blue: #0e75c0;
    --ring-blue: #1f4fa8;
    --mark-blue: #2b48b8;
    --text-light: #ffffff;
  }
  * { margin: 0; padding: 0; box-sizing: border-box; }
  html, body {
    width: 1200px; height: 900px; overflow: hidden;
    background: var(--stage);
  }
  .canvas { position: relative; width: 1200px; height: 900px; }

  .card {
    position: absolute;
    width: 520px; height: 300px;
    border-radius: 22px;
    overflow: hidden;
    background: var(--card-white);
    box-shadow: 0 10px 28px rgba(20, 30, 60, 0.18);
  }

  /* Front card */
  .card-front { left: 90px; top: 120px; }
  .front-brand {
    position: absolute; left: 0; right: 0; top: 112px;
    display: flex; align-items: center; justify-content: center; gap: 18px;
  }
  .brand-dot {
    width: 66px; height: 66px; border-radius: 50%;
    background: var(--mark-blue);
  }
  .brand-name {
    font-family: "Montserrat", sans-serif;
    font-weight: 800; font-size: 62px; letter-spacing: 1px;
    color: var(--navy); line-height: 1;
  }
  .front-web {
    position: absolute; left: 0; right: 0; bottom: 34px;
    text-align: center;
    font-family: "Lato", sans-serif; font-size: 16px; letter-spacing: 0.5px;
    color: var(--navy);
  }
  .front-web strong { font-weight: 700; }

  /* Back card */
  .card-back { left: 590px; top: 480px; }
  .back-shapes { position: absolute; inset: 0; }
  .contact {
    position: absolute; left: 78px; top: 104px;
    font-family: "Lato", sans-serif; color: var(--text-light);
  }
  .contact-name {
    font-family: "Montserrat", sans-serif;
    font-weight: 700; font-size: 23px; letter-spacing: 0.5px; line-height: 1.1;
  }
  .contact-role { font-size: 13px; line-height: 1.2; margin: 3px 0 10px 14px; }
  .contact-address { font-size: 14px; line-height: 1.3; margin-left: 30px; margin-bottom: 8px; }
  .contact-list { list-style: none; margin-left: 40px; font-size: 14px; line-height: 1.35; }
  .contact-list li { display: flex; align-items: center; gap: 9px; }
  .contact-list svg { width: 11px; height: 11px; flex: none; }
  .contact-list strong { font-weight: 700; }
</style>
</head>
<body>
<main class="canvas">

  <section class="card card-front" aria-label="Card front">
    <div class="front-brand">
      <span class="brand-dot"></span>
      <span class="brand-name">Korvel</span>
    </div>
    <p class="front-web">www.<strong>korvelpartsco</strong>.com</p>
  </section>

  <section class="card card-back" aria-label="Card back">
    <svg class="back-shapes" width="520" height="300" viewBox="0 0 520 300">
      <defs>
        <radialGradient id="markShade" cx="0.35" cy="0.3" r="0.75">
          <stop offset="0" stop-color="#3d63d6"/>
          <stop offset="1" stop-color="#23339c"/>
        </radialGradient>
      </defs>
      <rect width="520" height="300" fill="var(--brand-blue)"/>
      <circle cx="440" cy="95" r="175" fill="var(--card-white)" stroke="var(--ring-blue)" stroke-width="4"/>
      <rect x="410" y="-10" width="120" height="60" fill="var(--card-white)"/>
      <circle cx="425" cy="100" r="76" fill="url(#markShade)"/>
      <rect x="-12" y="172" width="44" height="100" rx="14" fill="var(--card-white)"/>
    </svg>

    <div class="contact">
      <h1 class="contact-name">Marta Ellison</h1>
      <p class="contact-role">Director</p>
      <p class="contact-address">P.O. Box 3380<br>Fenwick, OH 44219</p>
      <ul class="contact-list">
        <li>
          <svg viewBox="0 0 12 12" aria-hidden="true"><path d="M2.5 1h2l1 3-1.3 1a6 6 0 0 0 2.8 2.8l1-1.3 3 1v2a1 1 0 0 1-1 1A9.5 9.5 0 0 1 1.5 2a1 1 0 0 1 1-1z" fill="#fff"/></svg>
          <span>+330 5814-2297</span>
        </li>
        <li>
          <svg viewBox="0 0 12 12" aria-hidden="true"><rect x="1" y="2.5" width="10" height="7" rx="1" fill="none" stroke="#fff" stroke-width="1.2"/><path d="M1.5 3l4.5 3.5L10.5 3" fill="none" stroke="#fff" stroke-width="1.2"/></svg>
          <span>info@korvelpartsco.com</span>
        </li>
        <li>
          <svg viewBox="0 0 12 12" aria-hidden="true"><circle cx="6" cy="6" r="5" fill="none" stroke="#fff" stroke-width="1.1"/><ellipse cx="6" cy="6" rx="2.2" ry="5" fill="none" stroke="#fff" stroke-width="1"/><path d="M1 6h10" stroke="#fff" stroke-width="1"/></svg>
          <span>www.<strong>korvelpartsco</strong>.com</span>
        </li>
      </ul>
    </div>
  </section>

</main>
</body>
</html>
```